Lumbra Deckworks Company (southern african focus for now) needs a e-commerce website

We need a website design for a playing card company based in Southern Africa/United States. We make locally-sourced playing cards (standard 52 card deck, with customized fronts and backs) for everyone and collaborate with local artists to uplift their talents, while celebrating their nation's culture, heritage, beauty and identity. We would like to see designs that use the colours blue (see flag of Eswatini as starting product), white and some red accents (or your recommendation). The final design should communicate elegance, fun and sustainable prosperity.

Target Market(s)

Everyone loves playing cards. From the solo adventurer to the party host, first time learner or expert, young, middle and old, we need to attract a broad audience that appreciates the finer things and supports sustainable, environmentally contentiousness causes that support the local economy and uplift local talent - thing global, act local.

Number of Pages Required

4 page

Font styles to use
Serif
Sans Serif

Requirements
Must have
• Pages to include Home (Main), About (Our Story), Shop and Contact
Nice to have
• While designs may be static, elements of graceful movement would be desirable. Perhaps functionality of scrolling down on homepage showing playing cards in use, front and back. Quindle and Zorvax store's capture that elegant yet rich look.
Should not have
• Too many products. We focus on 1-2.

```html
<!DOCTYPE html>
<html lang="en">
<head>
<meta charset="utf-8">
<title>Lumbra – About</title>
<link href="https://fonts.googleapis.com/css2?family=Poppins:wght@400;500&family=Cormorant+Garamond:wght@500&display=swap" rel="stylesheet">
<style>
:root{
  --ink:#111111;
  --muted:#555555;
  --accent:#d11a1a;
  --bar:#333333;
  --paper:#f4f4f4;
  --band:#e8e8e8;
  --white:#ffffff;
  --flag-blue:#4a6fc4;
  --flag-red:#b8232b;
  --flag-gold:#f2c200;
}
*{margin:0;padding:0;box-sizing:border-box}
html,body{width:799px;height:1200px;overflow:hidden}
body{position:relative;background:var(--paper);font-family:'Poppins',sans-serif;color:var(--ink)}
.abs{position:absolute}
.site-header{left:0;top:0;width:799px;height:70px;background:var(--bar)}
.brand{left:58px;top:22px;display:flex;align-items:center;gap:7px;color:var(--white);font-family:'Cormorant Garamond',serif;font-size:19px;font-weight:500}
.brand-dot{width:14px;height:14px;border-radius:50%;background:var(--white)}
.nav a{position:absolute;top:29px;color:var(--white);font-size:10.5px;text-decoration:none;line-height:1}
.nav .current{border-bottom:1px solid var(--white);padding-bottom:3px}
.region{left:643px;top:25px;width:97px;height:27px;border:1px solid var(--white);color:var(--white);font-size:10.5px;display:flex;align-items:center;gap:7px;padding-left:9px}
.region .flag{width:14px;height:14px;border-radius:50%;background:linear-gradient(var(--flag-blue) 0 25%,var(--flag-gold) 25% 32%,var(--flag-red) 32% 68%,var(--flag-gold) 68% 75%,var(--flag-blue) 75%)}
.region .caret{width:0;height:0;border-left:4px solid transparent;border-right:4px solid transparent;border-top:5px solid var(--white);margin-left:4px}
.hero-title{left:0;top:111px;width:799px;text-align:center;font-size:28px;font-weight:500;line-height:35px}
.hero-title .tag{color:var(--accent)}
.mission{left:116px;top:317px;width:270px;font-size:14px;line-height:21px;font-weight:500}
.product-art{left:425px;top:275px;width:374px;height:200px;border-radius:14px;background:linear-gradient(120deg,var(--flag-blue) 0%,var(--flag-red) 35%,var(--flag-gold) 45%,var(--flag-red) 55%,var(--flag-blue) 100%);opacity:.92}
.people{left:0;top:559px;width:799px;height:536px;background:var(--band)}
.people-title{left:116px;top:596px;font-size:26px;font-weight:500}
.people-copy{left:116px;top:659px;width:280px;font-size:14px;line-height:21px;color:#333}
.people-copy p+p{margin-top:19px}
.lead-photo{left:442px;top:528px}
.member-name{font-size:17px;font-weight:500;line-height:1.2}
.member-role{font-size:14px;color:var(--muted);line-height:1.2}
.lead-caption{left:380px;top:803px;width:140px;text-align:right}
.team-photo{top:896px}
.team-caption{top:1005px}
.site-footer{left:0;top:1095px;width:799px;height:105px;background:var(--bar)}
.footer-text{color:var(--white)}
.footer-brand{left:44px;top:1120px;display:flex;align-items:center;gap:10px;font-family:'Cormorant Garamond',serif;font-size:30px;font-weight:500}
.footer-brand .brand-dot{width:22px;height:22px}
.footer-links{left:303px;top:1117px;font-size:8.5px;line-height:19.5px}
.footer-contacts{left:400px;top:1117px;font-size:8.5px;line-height:19.5px}
.footer-contacts div{display:flex;align-items:center;gap:5px}
.socials{left:553px;top:1128px;display:flex;gap:12px;font-size:9px;line-height:14px}
.socials span{display:flex;align-items:center;gap:4px}
.socials i{width:12px;height:12px;border:1.5px solid var(--white);border-radius:50%}
.copyright{left:553px;top:1160px;font-size:6.5px}
</style>
</head>
<body>
<header class="site-header abs">
  <div class="brand abs"><span class="brand-dot"></span>Lumbra</div>
  <nav class="nav">
    <a style="left:232px">Home</a>
    <a class="current" style="left:301px">About</a>
    <a style="left:370px">Collections</a>
    <a style="left:466px">Contact</a>
  </nav>
  <div class="region abs"><span class="flag"></span>Eswatini<span class="caret"></span></div>
</header>

<h1 class="hero-title abs">We’re celebrating cultural heritage and local<br>artistic talent through playing cards<br><span class="tag">one card at a time.</span></h1>

<p class="mission abs">We’re environmentally sustainable, philanthropic, and doing this for the good of the country. It’s about celebrating our heritage, whilst celebrating our diversity</p>

<div class="product-art abs" role="img" aria-label="Eswatini flag playing cards fanned out beside their box"></div>

<section class="people abs"></section>
<h2 class="people-title abs">The People</h2>
<div class="people-copy abs">
  <p>Lorem ipsum dolor sit amet, consectetur adipiscing elit. Dapibus mauris ac, mauris egestas. Porta faucibus aenean leo varius id eros sed pharetra.</p>
  <p>Lorem ipsum dolor sit amet, consectetur adipiscing elit. Dapibus mauris ac, mauris egestas.</p>
</div>

<svg class="lead-photo abs" width="300" height="325" viewBox="0 0 300 325" role="img" aria-label="Portrait of team lead in a blue suit and red tie">
  <defs><linearGradient id="leadTone" x1="0" y1="0" x2="1" y2="1"><stop offset="0" stop-color="#dcdfe4"/><stop offset=".5" stop-color="#8a7a70"/><stop offset="1" stop-color="#3e5a8c"/></linearGradient></defs>
  <rect x="55" y="35" width="190" height="255" rx="26" fill="url(#leadTone)" transform="rotate(-30 150 162)"/>
</svg>
<div class="lead-caption abs"><div class="member-name">Mr. Abc Xyz</div><div class="member-role">Designation</div></div>

<svg class="team-photo abs" style="left:127px" width="130" height="135" viewBox="0 0 130 135" role="img" aria-label="Portrait of team member">
  <defs><linearGradient id="toneA" x1="0" y1="0" x2="1" y2="1"><stop offset="0" stop-color="#d8dadf"/><stop offset=".6" stop-color="#8a6650"/><stop offset="1" stop-color="#e9e9ec"/></linearGradient></defs>
  <rect x="25" y="15" width="80" height="105" rx="14" fill="url(#toneA)" transform="rotate(-30 65 67)"/>
</svg>
<svg class="team-photo abs" style="left:340px" width="130" height="135" viewBox="0 0 130 135" role="img" aria-label="Portrait of team member">
  <defs><linearGradient id="toneB" x1="0" y1="0" x2="1" y2="1"><stop offset="0" stop-color="#cfd2d6"/><stop offset=".6" stop-color="#9a8a80"/><stop offset="1" stop-color="#e4e2dc"/></linearGradient></defs>
  <rect x="25" y="15" width="80" height="105" rx="14" fill="url(#toneB)" transform="rotate(-30 65 67)"/>
</svg>
<svg class="team-photo abs" style="left:554px" width="130" height="135" viewBox="0 0 130 135" role="img" aria-label="Portrait of team member">
  <defs><linearGradient id="toneC" x1="0" y1="0" x2="1" y2="1"><stop offset="0" stop-color="#7fb3b0"/><stop offset=".6" stop-color="#5a3a2c"/><stop offset="1" stop-color="#eeeeee"/></linearGradient></defs>
  <rect x="25" y="15" width="80" height="105" rx="14" fill="url(#toneC)" transform="rotate(-30 65 67)"/>
</svg>
<div class="team-caption abs" style="left:115px"><div class="member-name">Ms. Def Ghi</div><div class="member-role" style="padding-left:12px">Designation</div></div>
<div class="team-caption abs" style="left:327px"><div class="member-name">Mr. Jkl Mno</div><div class="member-role" style="padding-left:13px">Designation</div></div>
<div class="team-caption abs" style="left:543px"><div class="member-name">Ms. Pqr Stu</div><div class="member-role" style="padding-left:10px">Designation</div></div>

<footer class="site-footer abs"></footer>
<div class="footer-brand footer-text abs"><span class="brand-dot"></span>Lumbra</div>
<div class="footer-links footer-text abs"><div>Corporate office</div><div>International Branch</div><div>Contact Us</div></div>
<div class="footer-contacts footer-text abs">
  <div><svg width="9" height="9" viewBox="0 0 10 10"><circle cx="5" cy="5" r="4.2" fill="none" stroke="#fff"/><path d="M3.4 3.2l1 1.6-.5.6c.4.7.9 1.2 1.6 1.6l.6-.5 1.5 1" fill="none" stroke="#fff" stroke-width=".8"/></svg>+268 7600 1122</div>
  <div><svg width="9" height="9" viewBox="0 0 10 10"><circle cx="5" cy="5" r="4.2" fill="none" stroke="#fff"/><path d="M3.4 3.2l1 1.6-.5.6c.4.7.9 1.2 1.6 1.6l.6-.5 1.5 1" fill="none" stroke="#fff" stroke-width=".8"/></svg>+268 7600 1122</div>
  <div><svg width="10" height="8" viewBox="0 0 10 8"><rect x=".5" y=".5" width="9" height="7" fill="none" stroke="#fff"/><path d="M.5 .5L5 4.5 9.5 .5" fill="none" stroke="#fff"/></svg>hello@lumbradecks.com</div>
</div>
<div class="socials footer-text abs"><span><i></i>Fablo</span><span><i></i>Chirpa</span><span><i></i>Linkr</span><span><i></i>Snapo</span></div>
<div class="copyright footer-text abs">© All Rights Reserved. Lumbra. 2020</div>
</body>
</html>
```